Brightwell Dwelling Services - Maintenance & Improvements

Handyman service - Total home improvement and maintenance

We do everything indoors, ie. carpentry, and outdoors, ie. garden maintenance

No job too small or too unusual

7 Days per week

I want the overall impression not to favour either gender ... eg. maybe don't use the word Handy'man' because we also have a Home Helper service .... but just stay with a generic theme of home improvement and maintenance

Industry/Entity Type

Home Improvement

Contact Information for Business Card

Brightwell Dwelling Services
7 Days per Week
Total Home Maintenance and Improvements
Handyman | Home Helper | Our (DIY) Task Mate
Ph: 0417 863 208
www.brightwelldwelling.com.au

Requirements
Must have
• The black and white image of various workers, as per attached

```html
<!DOCTYPE html>
<html lang="en">
<head>
<meta charset="utf-8">
<title>Brightwell Dwelling Services – Business Card</title>
<link href="https://fonts.googleapis.com/css2?family=Open+Sans:wght@400;600;700&display=swap" rel="stylesheet">
<style>
  :root {
    --backdrop: #2b2b2b;
    --card-black: #050505;
    --gold-light: #f0c13a;
    --gold-dark: #b88f1e;
    --gold-text: #e9b530;
    --white: #ffffff;
  }
  html, body {
    margin: 0;
    width: 1200px;
    height: 900px;
    overflow: hidden;
    background: var(--backdrop);
    font-family: "Open Sans", Arial, sans-serif;
  }
  .business-card {
    position: absolute;
    left: 75px;
    top: 150px;
    width: 1050px;
    height: 600px;
    background: var(--card-black);
    overflow: hidden;
    box-shadow: 0 10px 40px rgba(0,0,0,.5);
  }
  .card-shapes {
    position: absolute;
    inset: 0;
  }
  .brand-title {
    position: absolute;
    left: 120px;
    top: 78px;
    margin: 0;
    color: var(--white);
    text-align: center;
    text-shadow: 0 1px 3px rgba(0,0,0,.35);
  }
  .brand-title .title-small {
    display: block;
    font-size: 26px;
    font-weight: 700;
    line-height: 1.1;
  }
  .brand-title .title-large {
    display: block;
    font-size: 46px;
    font-weight: 400;
    line-height: 1.15;
    letter-spacing: 1px;
  }
  .contact-block {
    position: absolute;
    right: 40px;
    top: 182px;
    text-align: right;
    color: var(--gold-text);
  }
  .contact-block .service-name {
    font-size: 30px;
    font-weight: 700;
    margin-right: 38px;
    line-height: 1.2;
  }
  .contact-line {
    display: flex;
    justify-content: flex-end;
    align-items: center;
    gap: 12px;
    font-size: 24px;
    line-height: 1.45;
    letter-spacing: .5px;
  }
  .contact-line svg {
    width: 24px;
    height: 24px;
    fill: var(--gold-text);
  }
  .brand-mark {
    position: absolute;
    left: 60px;
    top: 370px;
    display: flex;
    align-items: center;
    gap: 16px;
    color: var(--gold-text);
    font-size: 30px;
    font-weight: 600;
  }
  .brand-mark .mark-square {
    width: 44px;
    height: 44px;
    background: var(--gold-text);
  }
  .web-address {
    position: absolute;
    right: 78px;
    top: 452px;
    color: var(--gold-text);
    font-size: 26px;
    letter-spacing: 1px;
  }
  .service-line {
    position: absolute;
    left: 50px;
    right: 50px;
    top: 510px;
    color: var(--gold-text);
    font-size: 26px;
    letter-spacing: 1px;
    white-space: nowrap;
  }
</style>
</head>
<body>
  <div class="business-card">
    <svg class="card-shapes" viewBox="0 0 1050 600" aria-hidden="true">
      <defs>
        <linearGradient id="goldBand" x1="0" y1="0" x2="1" y2="1">
          <stop offset="0" stop-color="#b88f1e"/>
          <stop offset="0.6" stop-color="#f0c13a"/>
          <stop offset="1" stop-color="#b88f1e"/>
        </linearGradient>
      </defs>
      <path d="M0,0 H1050 V138 C880,150 720,190 560,240 C400,292 200,315 0,325 Z" fill="url(#goldBand)"/>
      <path d="M0,325 C200,315 400,292 560,240 C720,190 880,150 1050,138 V150 C880,160 720,200 560,252 C400,304 200,330 0,342 Z" fill="#ffffff"/>
    </svg>

    <h1 class="brand-title">
      <span class="title-small">Brightwell</span>
      <span class="title-large">Dwelling Services</span>
    </h1>

    <div class="contact-block">
      <div class="service-name">Home Helper</div>
      <div class="contact-line">
        <span>Our (DIY) Task Mate</span>
        <svg viewBox="0 0 24 24" aria-label="phone"><path d="M6.6 10.8a15 15 0 0 0 6.6 6.6l2.2-2.2a1 1 0 0 1 1-.25 11.4 11.4 0 0 0 3.6.57 1 1 0 0 1 1 1V20a1 1 0 0 1-1 1A17 17 0 0 1 3 4a1 1 0 0 1 1-1h3.5a1 1 0 0 1 1 1c0 1.25.2 2.45.57 3.57a1 1 0 0 1-.25 1z"/></svg>
      </div>
      <div class="contact-line">
        <span>0417 863 208</span>
        <svg viewBox="0 0 24 24" aria-label="web"><path d="M12 2a10 10 0 1 0 0 20 10 10 0 0 0 0-20zm6.9 6h-2.9a15 15 0 0 0-1.4-3.6A8 8 0 0 1 18.9 8zM12 4c.8 1.2 1.5 2.5 1.9 4h-3.8c.4-1.5 1.1-2.8 1.9-4zM4.3 14a8 8 0 0 1 0-4h3.4a16 16 0 0 0 0 4zm.8 2h2.9a15 15 0 0 0 1.4 3.6A8 8 0 0 1 5.1 16zM8 8H5.1a8 8 0 0 1 4.3-3.6A15 15 0 0 0 8 8zm4 12c-.8-1.2-1.5-2.5-1.9-4h3.8c-.4 1.5-1.1 2.8-1.9 4zm2.3-6H9.7a14 14 0 0 1 0-4h4.6a14 14 0 0 1 0 4zm.3 5.6a15 15 0 0 0 1.4-3.6h2.9a8 8 0 0 1-4.3 3.6zm1.7-5.6a16 16 0 0 0 0-4h3.4a8 8 0 0 1 0 4z"/></svg>
      </div>
    </div>

    <div class="brand-mark">
      <span class="mark-square"></span>
      <span>Brightwell Dwelling Services</span>
    </div>

    <div class="web-address">www.brightwelldwelling.com.au</div>
    <div class="service-line">7 Days per Week Total Home Maintenance | Improvements Handyman</div>
  </div>
</body>
</html>
```